Business card for denture clinic Veltrimora

We need a new business card with our new logo. We are a denture clinic in New Zealand with our target market being 45+ years old. We would need a space on the back to write our patients next appointment on. We would space for only one appointment rather than a list. We will attach a photo showing an example of this. But of course, we would like to see your twist on this. We want it to be bold and easy to read and a good mixture of professional but modern. We have attached our logo to be used on the card.

Target Market(s)

People aged 45+ needing dentures

Industry/Entity Type

Dental

Contact Information for Business Card

We want our logo on the front and the space to write an appointment on the back. I've attached an example our our old business card showing this. We need to have the technicians details on the front.

Font styles to use
Sans Serif

Colors
0255a3
919191
fbfbfb

Requirements
Must have
• The following details:
• Liam Dorsett BDT, PGDipCDentTech Calverin
• Dental Prosthetist
• Phone numbers: 0800 47 3125
• 09 572 1394
• Email: liam@veltrimora.co.nz
• www.veltrimora.co.nz
• Address: 14 Marlow Crest Road
• Halbrook West
• Auckland 0793
Nice to have
• We would like our business cards to have more than just two colours as we want them to be more vibrant. We have uploaded an example of a business card we liked that showed this.

```html
<!DOCTYPE html>
<html lang="en">
<head>
<meta charset="utf-8">
<title>Veltrimora business card</title>
<link rel="stylesheet" href="https://fonts.googleapis.com/css2?family=Open+Sans:ital,wght@0,400;0,600;1,400&display=swap">
<style>
  :root {
    --brand-blue: #0270bb;
    --ink: #2e2e2e;
    --grey: #5b5b5b;
    --card-white: #ffffff;
    --field: #f4f4f4;
    --backdrop: #efebe5;
  }
  * { box-sizing: border-box; margin: 0; padding: 0; }
  html, body {
    width: 1200px; height: 987px; overflow: hidden;
    background: var(--backdrop);
    font-family: "Open Sans", Arial, sans-serif;
  }
  .canvas { position: relative; width: 1200px; height: 987px; }
  .card {
    position: absolute; width: 616px; height: 352px;
    border-radius: 20px; overflow: hidden;
    box-shadow: 0 2px 6px rgba(0,0,0,0.18);
  }
  .card-front { left: 293px; top: 130px; background: var(--card-white); }
  .card-back { left: 292px; top: 505px; background: var(--brand-blue); }

  .technician {
    position: absolute; left: 79px; top: 141px; width: 240px;
    text-align: center; line-height: 1.25;
  }
  .technician-name { color: var(--brand-blue); font-weight: 600; font-size: 20px; }
  .technician-name small { font-size: 16px; }
  .technician-quals { color: var(--brand-blue); font-weight: 600; font-size: 16px; }
  .technician-role { color: var(--ink); font-size: 16px; margin-top: 2px; }

  .brand { position: absolute; right: 24px; top: 35px; text-align: center; width: 220px; }
  .brand-square {
    display: block; width: 44px; height: 44px; margin: 0 auto 6px;
    background: var(--brand-blue);
  }
  .brand-name {
    color: var(--brand-blue); font-size: 22px; font-weight: 600;
    letter-spacing: 1.5px; text-transform: uppercase;
  }

  .contact {
    position: absolute; right: 24px; top: 156px; text-align: right;
    color: var(--grey); font-size: 16px; line-height: 22px;
  }
  .address { margin-bottom: 11px; }
  .contact .label { color: var(--brand-blue); font-weight: 600; }
  .contact .phone { color: var(--ink); }

  .back-mark {
    position: absolute; left: 250px; top: 62px; width: 115px; height: 114px;
    background: var(--card-white); border-radius: 2px;
    display: flex; align-items: center; justify-content: center;
    color: var(--brand-blue); font-size: 15px; font-weight: 600;
  }
  .appointment-title {
    position: absolute; left: 0; right: 0; top: 220px; text-align: center;
    color: var(--card-white); font-size: 21px; font-weight: 600;
  }
  .appointment-field {
    position: absolute; left: 30px; top: 273px; width: 556px; height: 42px;
    background: var(--field); border-radius: 21px;
    color: var(--brand-blue); font-style: italic; font-size: 17px;
  }
  .appointment-field span { position: absolute; top: 9px; }
  .field-date { left: 22px; }
  .field-divider {
    position: absolute; left: 278px; top: 5px; width: 2px; height: 32px;
    background: var(--brand-blue);
  }
  .field-time { left: 300px; }
  .field-ampm { right: 22px; }
</style>
</head>
<body>
<div class="canvas">
  <section class="card card-front">
    <div class="technician">
      <p class="technician-name">LIAM DORSETT <small>BDT</small></p>
      <p class="technician-quals">PGDipCDentTech Calverin</p>
      <p class="technician-role">Dental Prosthetist</p>
    </div>
    <div class="brand">
      <span class="brand-square"></span>
      <p class="brand-name">Veltrimora</p>
    </div>
    <div class="contact">
      <p class="address">14 Marlow Crest Road<br>Halbrook West<br>Auckland 0793</p>
      <p><span class="label">P :</span> <span class="phone">0800 47 3125</span></p>
      <p><span class="label">C :</span> <span class="phone">09 572 1394</span></p>
      <p>liam@veltrimora.co.nz</p>
      <p>www.veltrimora.co.nz</p>
    </div>
  </section>

  <section class="card card-back">
    <div class="back-mark">Veltrimora</div>
    <p class="appointment-title">NEXT APPOINTMENT</p>
    <div class="appointment-field">
      <span class="field-date">date:</span>
      <i class="field-divider"></i>
      <span class="field-time">time:</span>
      <span class="field-ampm">am/pm</span>
    </div>
  </section>
</div>
</body>
</html>
```